Wordpress coded website (5 page-home page, contact form & 3 common pages) for Skiing event

I would like a WordPress site designed for our Ski & Snowboard event. The site is to have 5 total pages.

Hosting has been setup (Bright Hostings) and WordPress installed.

Requirements:
Front page with Landscape slide, Friendly feed, 4 menu items, footer and small description section.

3 Separate pages to be created, with a similar layout with landscape image slider and large text section (content provided)

1 Contact us page with the below form sections
- Name
- School
- Position
- Email
- Phone
- Message

Target Market(s)

School teachers and school students

Industry/Entity Type

Tourism

Number of Pages Required

5+ page

Colors

Designer to choose colors to be used in the design.

Requirements
Must have
• Must include event logo attached in brief. Must include Friendly feed on homepage

```html
<!DOCTYPE html>
<html lang="en">
<head>
<meta charset="utf-8">
<title>Kestrel Peak Ski Challenge</title>
<link href="https://fonts.googleapis.com/css2?family=Lato:wght@400;700&display=swap" rel="stylesheet">
<style>
:root{
  --blue:#1a9ae2;
  --navy:#2f4a8c;
  --ink:#222;
  --text:#333;
  --dark:#1d1d1d;
  --darker:#111;
  --line:#d6d6d6;
  --white:#fff;
}
*{box-sizing:border-box;margin:0;padding:0}
html,body{width:1017px;height:1200px;overflow:hidden}
body{font-family:'Lato',sans-serif;color:var(--text);background:var(--white);position:relative}
.abs{position:absolute}
.topbar-email{left:515px;top:0;width:280px;height:30px;background:#2a2a2a;color:#fff;font-size:13.5px;display:flex;align-items:center;gap:8px;padding-left:20px;clip-path:polygon(0 0,100% 0,100% 100%,10px 100%)}
.topbar-phone{left:790px;top:0;width:145px;height:30px;background:var(--blue);color:#fff;font-size:13.5px;display:flex;align-items:center;gap:8px;padding-left:13px;clip-path:polygon(0 0,100% 0,calc(100% - 10px) 100%,0 100%)}
.topbar-icon{width:20px;height:20px;border-radius:50%;background:#fff;display:flex;align-items:center;justify-content:center}
.brand-tab{left:83px;top:0;width:150px;height:176px;background:#fff;box-shadow:0 2px 6px rgba(0,0,0,.15);clip-path:polygon(0 0,100% 0,100% 150px,50% 176px,0 150px);display:flex;flex-direction:column;align-items:center;justify-content:center;gap:8px;z-index:3}
.brand-name{font-size:17px;font-weight:700;color:var(--blue);text-align:center;line-height:1.2}
.brand-dot{width:26px;height:26px;border-radius:50%;background:var(--blue)}
.nav{left:395px;top:62px;display:flex;align-items:center}
.nav a{font-size:15px;color:var(--ink);text-decoration:none;padding:0 32px;border-left:1px solid #ccc;line-height:16px}
.nav a:first-child{border-left:none;padding-left:24px}
.nav a.active{color:var(--blue);font-weight:700}
.nav-marker{left:430px;top:86px;width:16px;height:16px;border-radius:50%;background:var(--blue)}
.hero{left:0;top:113px;width:1017px;height:462px;background:linear-gradient(180deg,#2d3a2f 0%,#5c6a63 35%,#bfc4c6 62%,#e3e6ea 80%,#6d6f72 100%)}
.hero-arrow{top:330px;width:34px;height:36px;background:rgba(0,0,0,.35);display:flex;align-items:center;justify-content:center}
.hero-title{left:0;top:514px;width:1017px;text-align:center;color:#fff;font-size:34px;font-weight:700;text-shadow:0 1px 3px rgba(0,0,0,.4)}
.about-title{left:84px;top:613px;font-size:27px;font-weight:700;color:var(--blue)}
.about-mark{left:84px;top:661px;width:18px;height:20px;border-radius:50%;background:#c9c9c9}
.about-rule{left:115px;top:671px;width:558px;height:2px;background:var(--line)}
.about-body{left:85px;top:700px;width:590px;font-size:13.5px;line-height:23.5px}
.about-body .date{font-weight:700;color:var(--ink)}
.about-body .notes{margin-top:6px}
.feed{left:711px;top:619px;width:222px;height:249px;border:2px solid var(--navy);background:#fff}
.feed-head{height:32px;background:var(--navy);color:#fff;font-size:11px;display:flex;justify-content:space-between;align-items:center;padding:0 12px}
.feed-head b{font-size:11px}
.feed-item{display:flex;gap:8px;margin:0 10px;padding:10px 0 8px;border-bottom:1px dotted #ccc}
.feed-item:last-of-type{border-bottom:none}
.feed-thumb{width:44px;height:36px;flex:none;background:linear-gradient(135deg,#3f5f7a,#9aa9b3)}
.feed-link{color:#3b5aa8;font-size:10px;line-height:14px}
.feed-meta{font-size:8px;color:#333;margin-top:5px}
.feed-foot{position:absolute;left:0;bottom:0;width:100%;border-top:1px solid #ddd;font-size:10px;color:#555;padding:8px 10px}
.footer{left:0;top:912px;width:1017px;height:251px;background:var(--dark);color:#fff}
.foot-h{position:absolute;top:33px;font-size:17px;font-weight:700;text-transform:uppercase}
.foot-h span{color:var(--blue)}
.foot-rule{position:absolute;top:62px;height:1px;background:#444}
.foot-rule::before{content:"";position:absolute;left:0;top:0;width:24px;height:1px;background:#999}
.vsep{position:absolute;top:45px;width:1px;height:175px;background:#333}
.links{position:absolute;left:85px;top:72px;list-style:none;font-size:13.5px}
.links li{height:30px;line-height:30px}
.links li::before{content:"•";margin-right:6px;font-size:9px}
.contact{position:absolute;left:255px;top:73px;font-size:11.5px;line-height:18px}
.contact strong{font-size:14px;display:block;margin-bottom:1px}
.contact-row{display:flex;align-items:center;gap:10px;margin-top:12px}
.form{position:absolute;left:517px;top:75px;width:218px}
.field{height:29px;border:1px solid #444;background:#1b1b1b;font-size:11px;color:#ddd;padding:8px 10px;margin-bottom:6px}
.field.msg{height:36px}
.submit{width:87px;height:29px;background:var(--blue);color:#fff;font-size:14px;font-weight:700;display:flex;align-items:center;justify-content:center;margin-top:2px}
.foot-badge{position:absolute;left:795px;top:42px;width:140px;height:180px;background:#4a4a4a;clip-path:polygon(50% 0,100% 22%,100% 72%,50% 100%,0 72%,0 22%);display:flex;align-items:center;justify-content:center;text-align:center;color:#bdbdbd;font-size:15px;font-weight:700;line-height:1.25}
.bottombar{left:0;top:1163px;width:1017px;height:37px;background:var(--darker);color:#fff;font-size:11.5px}
.copy{position:absolute;left:85px;top:11px}
.social{position:absolute;right:84px;top:8px;display:flex;gap:7px}
.social i{width:20px;height:20px;border-radius:50%;background:#fff;display:block}
</style>
</head>
<body>

<div class="abs topbar-email"><span class="topbar-icon"><svg width="10" height="8" viewBox="0 0 10 8"><rect x="0.5" y="0.5" width="9" height="7" fill="none" stroke="#222"/><path d="M0.5 0.5 L5 4.5 L9.5 0.5" fill="none" stroke="#222"/></svg></span>enquiry@kestrelskichallenge.com.au</div>
<div class="abs topbar-phone"><span class="topbar-icon"><svg width="10" height="8" viewBox="0 0 10 8"><rect x="0.5" y="0.5" width="9" height="7" fill="none" stroke="#1a9ae2"/><path d="M0.5 0.5 L5 4.5 L9.5 0.5" fill="none" stroke="#1a9ae2"/></svg></span>02 5550 1842</div>

<div class="abs brand-tab"><span class="brand-dot"></span><span class="brand-name">Kestrel Peak<br>Ski Challenge</span></div>

<nav class="abs nav">
  <a class="active">Home</a><a>Event</a><a>Mt Kestrel</a><a>Itinerary</a><a>Contact Us</a>
</nav>
<span class="abs nav-marker"></span>

<div class="abs hero" role="img" aria-label="Snow-covered alpine lodges among pine trees in winter"></div>
<div class="abs hero-arrow" style="left:27px"><svg width="10" height="14"><path d="M8 1 L2 7 L8 13" stroke="#fff" stroke-width="2" fill="none"/></svg></div>
<div class="abs hero-arrow" style="left:955px"><svg width="10" height="14"><path d="M2 1 L8 7 L2 13" stroke="#fff" stroke-width="2" fill="none"/></svg></div>
<h1 class="abs hero-title">Welcome To About Kestrel Peak Ski Challenge</h1>

<h2 class="abs about-title">About Kestrel Peak Ski Challenge</h2>
<span class="abs about-mark"></span>
<span class="abs about-rule"></span>
<div class="abs about-body">
  <p class="date">Wednesday 11th July &amp; Thursday 12th July 2018.</p>
  <p>The Mt Kestrel Ski Challenge is the first event of its kind in the Southern Hemisphere offering high school students from Australia to face off against New Zealand locals on the ski fields of Mt Kestrel. With no race experience necessary, the event provides a great fun experience for those enjoying their first time on the slopes as well as providing a chance for experienced skiers and snowboarders to test themselves against the clock and other competitors.</p>
  <p class="notes"><strong>Notes:</strong> No experience necessary badge to appear on page</p>
</div>

<aside class="abs feed">
  <div class="feed-head"><span>Recent Activity</span><b>Friendly</b></div>
  <div class="feed-item"><div class="feed-thumb" role="img" aria-label="Lodge photo"></div><div><div class="feed-link">Lorem ipsum dolor sit amet the consectetuer adipi.</div><div class="feed-meta">2 people recommended this.</div></div></div>
  <div class="feed-item"><div class="feed-thumb" role="img" aria-label="Ski equipment photo"></div><div><div class="feed-link">Lorem ipsum dolor sit amet the adipiscing elit, sed di nonummy</div><div class="feed-meta">3 people recommended this.</div></div></div>
  <div class="feed-item"><div class="feed-thumb" role="img" aria-label="Skier photo"></div><div><div class="feed-link">Lorem ipsum dolor sit amet the consectetuer adipiscing.</div><div class="feed-meta">2 people recommended this.</div></div></div>
  <div class="feed-foot">Friendly Social Plugin</div>
</aside>

<footer class="abs footer">
  <h3 class="foot-h" style="left:83px">Quick <span>Links</span></h3>
  <span class="foot-rule" style="left:85px;width:108px"></span>
  <ul class="links"><li>Home</li><li>Event</li><li>Mt Kestrel</li><li>Itinerary</li><li>Contact Us</li></ul>
  <span class="vsep" style="left:221px"></span>

  <h3 class="foot-h" style="left:252px">Contact <span>Details</span></h3>
  <span class="foot-rule" style="left:254px;width:204px"></span>
  <div class="contact">
    <strong>Kestrel Peak Ski Challenge</strong>
    12 Summit Road, Snowline,<br>Alpine - 54321
    <div class="contact-row"><svg width="10" height="11" viewBox="0 0 10 11"><path d="M2 0 L4 2.5 L3 4 Q4 6.5 6.5 8 L8 7 L10 9 L8.5 11 Q1 9 0 1.5 Z" fill="#fff"/></svg>02 5550 1842</div>
    <div class="contact-row"><svg width="11" height="10" viewBox="0 0 11 10"><rect x="2.5" y="0" width="6" height="3" fill="#fff"/><rect x="0" y="3.5" width="11" height="4" fill="#fff"/><rect x="2.5" y="6" width="6" height="4" fill="#fff" stroke="#1d1d1d"/></svg>02 5550 1842</div>
    <div class="contact-row"><svg width="11" height="8" viewBox="0 0 11 8"><rect x="0.5" y="0.5" width="10" height="7" fill="#fff"/><path d="M0.5 0.5 L5.5 4.5 L10.5 0.5" fill="none" stroke="#1d1d1d"/></svg>enquiry@kestrelskichallenge.com.au</div>
  </div>
  <span class="vsep" style="left:485px"></span>

  <h3 class="foot-h" style="left:516px">Quick <span>Inquiry</span></h3>
  <span class="foot-rule" style="left:518px;width:218px"></span>
  <div class="form">
    <div class="field">Name</div>
    <div class="field">Email</div>
    <div class="field msg">Message</div>
    <div class="submit">SUBMIT</div>
  </div>
  <span class="vsep" style="left:764px"></span>

  <div class="foot-badge">Kestrel Peak<br>Ski Challenge</div>
</footer>

<div class="abs bottombar">
  <span class="copy">Copyright © 2017 Kestrel Peak Ski Challenge. All Right Reserved.</span>
  <div class="social"><i></i><i></i><i></i><i></i></div>
</div>

</body>
</html>
```